Meridale Accountants needs a stationery design

We need a stationery design for our new innovative accountancy practise - it is to look professional and reliable but also minimalist, crisp, innovative and fresh. Avoid the use of block colour. You must include letterhead.

We look after business clients and help them get started and grow to successful companies. We provide a range of software, accounting, taxation and business consulting services to these clients.

This is a spin off from our more traditional existing practise - we would like to use the same green and blue.

The final design should communicate professional expertise coupled with innovative technology and personal care. The font of the type should reflect this - so far we have received standard font only.

We need business cards, letterhead, with comp slips, We need to see the whole set to form a view, not just the businesscard

I have uploaded the colours that we want to use from our existing letterhead, being the green and blue. We need to use the KTR logo - also enclosed - please use the text from the enclosed letterhead, but don't refer to this for design purposes - this was our temporary draft only.

Target Market(s)

Small to medium companies, high wealth investor clients

Industry/Entity Type

Professional Service

Requirements
Must have
• Crisp, simple design but evoking innovation, technology, competence and difference.
• So far the designs are too standard and not showing innovation.

```html
<!DOCTYPE html>
<html lang="en">
<head>
<meta charset="utf-8">
<title>Meridale Accountants – Stationery Set</title>
<link href="https://fonts.googleapis.com/css2?family=Jost:wght@400;500&family=PT+Sans+Narrow:wght@400;700&display=swap" rel="stylesheet">
<style>
  :root{
    --bg:#d1e09c;
    --green:#7aa23a;
    --green-dark:#5f8a24;
    --green-light:#a9c868;
    --blue:#1c4c9c;
    --paper:#ffffff;
    --ink:#2c3e6e;
  }
  *{box-sizing:border-box;margin:0;padding:0}
  html,body{width:1200px;height:900px;overflow:hidden;background:var(--bg)}
  body{position:relative;font-family:"PT Sans Narrow",sans-serif;color:var(--ink)}
  .piece{position:absolute;background:var(--paper);overflow:hidden}

  /* wordmark */
  .wordmark{font-family:"Jost",sans-serif;font-weight:400;color:var(--green-dark);line-height:1;display:inline-block;text-align:center}
  .wordmark .w1{display:block;letter-spacing:.2em}
  .wordmark .w2{display:block;letter-spacing:.32em;margin-top:2px}
  .wordmark.on-green{color:#fff}

  /* footer bands */
  .band{position:absolute;left:0;right:0;bottom:0;height:4px;background:var(--green)}
  .band::after{content:"";position:absolute;right:0;bottom:0;width:26%;height:4px;background:var(--blue)}

  /* member note with a plain square */
  .badge{display:inline-block;width:14px;height:14px;background:var(--blue);vertical-align:middle;flex:none}
  .member{display:flex;align-items:center;gap:5px;font-size:5px;color:var(--ink);line-height:1.2;white-space:nowrap}

  .mini-foot{position:absolute;left:10px;bottom:10px;width:215px;font-size:5.5px;color:var(--ink);line-height:1.7;white-space:nowrap}

  /* minis */
  .mini-card{width:84px;height:34px;display:flex;align-items:center;justify-content:center}
  .mini-card .wordmark{font-size:10px}
  .mini-card .wordmark .w2{font-size:4px}

  /* envelope front */
  .envelope{left:98px;top:150px;width:326px;height:165px}
  .envelope .wordmark{position:absolute;left:22px;top:20px;font-size:16px}
  .envelope .wordmark .w2{font-size:6px}
  .corner-member{position:absolute;right:10px;bottom:10px}

  /* open envelope */
  .envelope-open{left:88px;top:350px;width:328px;height:210px;background:var(--paper)}
  .envelope-open .flap{position:absolute;left:0;top:0;width:100%;height:90px}
  .envelope-open .wordmark{position:absolute;left:50%;top:128px;transform:translateX(-50%);font-size:16px}
  .envelope-open .wordmark .w2{font-size:6px}

  /* comp slip */
  .comp-slip{left:84px;top:598px;width:326px;height:160px}
  .comp-slip .wordmark{position:absolute;left:20px;top:20px;font-size:16px}
  .comp-slip .wordmark .w2{font-size:6px}
  .comp-slip .compliments{position:absolute;right:16px;top:20px;font-size:9px;color:var(--green-dark)}

  /* letterhead */
  .letterhead{left:456px;top:88px;width:334px;height:470px}
  .letterhead .wordmark{position:absolute;left:18px;top:26px;font-size:14px}
  .letterhead .wordmark .w2{font-size:5.5px}
  .letterhead .sender{position:absolute;right:16px;top:30px;text-align:right;font-size:5.5px;line-height:1.35;color:var(--blue)}
  .letterhead .sender strong{display:block;font-size:7.5px;color:var(--green-dark)}
  .letterhead .legal{position:absolute;left:40px;top:250px;width:320px;transform:rotate(-40deg);font-size:9px;color:#dbe6c8;white-space:nowrap}
  .letterhead .foot{position:absolute;left:18px;bottom:14px;right:16px;display:flex;align-items:flex-end;font-size:5px;line-height:1.55}
  .letterhead .col{padding-right:16px;margin-right:14px}
  .letterhead .col.services{border-right:1px solid var(--green)}
  .letterhead .col h4{font-size:6px;color:var(--green-dark);border-left:2px solid var(--green);border-right:2px solid var(--green);padding:0 4px;margin-bottom:3px;display:inline-block}
  .letterhead .col li{list-style:none;color:var(--ink)}
  .letterhead .col.services li::before{content:"▸ "}
  .letterhead .member{margin-left:auto}

  /* folder */
  .folder{left:776px;top:176px;width:330px;height:446px;background:linear-gradient(160deg,#8ab345 0%,#7ea63b 45%,#a7c66a 100%)}
  .folder .pattern{position:absolute;right:0;top:0;width:60%;height:100%;background:linear-gradient(120deg,rgba(255,255,255,0) 20%,rgba(255,255,255,.12) 100%)}
  .folder .wordmark{position:absolute;left:50%;top:186px;transform:translateX(-50%);font-size:30px}
  .folder .wordmark .w2{font-size:11px;margin-top:4px}
  .folder .legal{position:absolute;left:0;right:0;top:250px;text-align:center;font-size:7.5px;color:#fff}
  .folder .tab{position:absolute;left:0;right:0;bottom:0;height:4px;background:var(--green-dark)}
  .folder .tab::after{content:"";position:absolute;right:0;width:25%;height:4px;background:var(--green-light)}

  /* business card front */
  .card-front{left:440px;top:622px;width:284px;height:170px;border-radius:10px;background:linear-gradient(100deg,#7ea63b 0%,#96bb55 55%,#c3da8d 100%)}
  .card-front .wordmark{position:absolute;left:50%;top:50px;transform:translateX(-50%);font-size:22px}
  .card-front .wordmark .w2{font-size:8px;margin-top:3px}
  .card-front .details{position:absolute;left:0;right:0;top:120px;text-align:center;font-size:6px;line-height:1.8;color:#eef5df}
  .card-front .notch{position:absolute;left:50%;bottom:0;transform:translateX(-50%);width:18px;height:6px;background:var(--green-dark);border-radius:2px 2px 0 0}

  /* business card back */
  .card-back{left:746px;top:640px;width:280px;height:164px;border-radius:10px}
  .card-back .wordmark{position:absolute;left:28px;top:48px;font-size:16px}
  .card-back .wordmark .w2{font-size:6px}
  .card-back .divider{position:absolute;left:140px;top:20px;width:1.5px;height:128px;background:var(--green-dark)}
  .card-back .person{position:absolute;left:36px;top:110px}
  .card-back .person h3{font-family:"PT Sans Narrow",sans-serif;font-weight:700;font-size:11px;color:var(--blue)}
  .card-back .person p{font-size:7px;color:var(--green-dark)}
  .card-back .contacts{position:absolute;right:12px;top:54px;text-align:right;font-size:6.5px;line-height:1.7;color:var(--ink)}
  .card-back .contacts span{display:inline-flex;align-items:center;gap:4px}
  .card-back .contacts svg{width:6px;height:6px;fill:var(--blue)}
  .card-back .member{position:absolute;left:150px;bottom:28px;font-size:6px}
  .card-back .member .badge{width:20px;height:20px}
</style>
</head>
<body>

  <div class="piece mini-card" style="left:226px;top:90px">
    <span class="wordmark"><span class="w1">MERIDALE</span><span class="w2">ACCOUNTANTS</span></span>
  </div>
  <div class="piece mini-card" style="left:346px;top:93px">
    <span class="wordmark"><span class="w1">MERIDALE</span><span class="w2">ACCOUNTANTS</span></span>
  </div>

  <section class="piece envelope">
    <span class="wordmark"><span class="w1">MERIDALE</span><span class="w2">ACCOUNTANTS</span></span>
    <div class="mini-foot">
      <div>A : Suite 4B, Level 3, 12 Harlow Street, Penbrook NSW 2690 &nbsp; T : (02) 5550 1420 &nbsp; M : 0400 555 318</div>
      <div>P : P O Box 2208, Penbrook NSW 2690 &nbsp; E : clients@meridaleaccts.com.au</div>
      <div>W : meridaleaccts.com.au &nbsp; ABN 51 824 093 716</div>
    </div>
    <div class="member corner-member"><span>Meridale Accountants is a<br>KTR Practise</span><span class="badge"></span></div>
    <div class="band"></div>
  </section>

  <section class="piece envelope-open">
    <svg class="flap" viewBox="0 0 328 90" preserveAspectRatio="none">
      <polygon points="0,0 328,0 328,40 300,46 28,46 0,40" fill="#ffffff"/>
      <polygon points="20,46 308,46 290,88 38,88" fill="#86a84a"/>
      <polygon points="0,40 20,46 38,88 0,88" fill="#f3f3f3"/>
      <polygon points="328,40 308,46 290,88 328,88" fill="#f3f3f3"/>
    </svg>
    <span class="wordmark"><span class="w1">MERIDALE</span><span class="w2">ACCOUNTANTS</span></span>
  </section>

  <section class="piece comp-slip">
    <span class="wordmark"><span class="w1">MERIDALE</span><span class="w2">ACCOUNTANTS</span></span>
    <div class="compliments">With Compliments</div>
    <div class="mini-foot">
      <div>A : Suite 4B, Level 3, 12 Harlow Street, Penbrook NSW 2690 &nbsp; T : (02) 5550 1420 &nbsp; M : 0400 555 318</div>
      <div>P : P O Box 2208, Penbrook NSW 2690 &nbsp; E : clients@meridaleaccts.com.au</div>
      <div>W : meridaleaccts.com.au &nbsp; ABN 51 824 093 716</div>
    </div>
    <div class="member corner-member"><span>Meridale Accountants is a<br>KTR Practise</span><span class="badge"></span></div>
    <div class="band"></div>
  </section>

  <section class="piece letterhead">
    <span class="wordmark"><span class="w1">MERIDALE</span><span class="w2">ACCOUNTANTS</span></span>
    <div class="sender">
      <strong>Meridale Accountants</strong>
      Suite 4B, Level 3, 12 Harlow Street,<br>Penbrook NSW 2690<br>ABN 51 824 093 716
    </div>
    <div class="legal">Liability Limited by a Scheme Approved Under Professional Standards Legislation</div>
    <div class="foot">
      <div class="col services">
        <h4>Services</h4>
        <ul><li>Taxation</li><li>Business Consulting</li><li>Software</li><li>Accounting</li><li>Bookkeeping</li></ul>
      </div>
      <div class="col contact">
        <h4>Contact</h4>
        <ul><li>T : (02) 5550 1420</li><li>M : 0400 555 318</li><li>P : P O Box 2208, Penbrook NSW 2690</li><li>E : clients@meridaleaccts.com.au</li><li>W : meridaleaccts.com.au</li></ul>
      </div>
      <div class="member"><span>Meridale Accountants is a<br>KTR Practise</span><span class="badge"></span></div>
    </div>
    <div class="band"></div>
  </section>

  <section class="piece folder">
    <div class="pattern" role="img" aria-label="Faint repeating diagonal slogan texture"></div>
    <span class="wordmark on-green"><span class="w1">MERIDALE</span><span class="w2">ACCOUNTANTS</span></span>
    <p class="legal">Liability Limited by a Scheme Approved Under Professional Standards Legislation</p>
    <div class="tab"></div>
  </section>

  <section class="piece card-front">
    <span class="wordmark on-green"><span class="w1">MERIDALE</span><span class="w2">ACCOUNTANTS</span></span>
    <div class="details">
      W : meridaleaccts.com.au<br>
      A : Suite 4B, Level 3, 12 Harlow Street, Penbrook NSW 2690<br>
      P : P O Box 2208, Penbrook NSW 2690
    </div>
    <div class="notch"></div>
  </section>

  <section class="piece card-back">
    <span class="wordmark"><span class="w1">MERIDALE</span><span class="w2">ACCOUNTANTS</span></span>
    <div class="person"><h3>Mr. Example</h3><p>Chartered Accountant</p></div>
    <div class="divider"></div>
    <div class="contacts">
      <span>(02) 5550 1420 <svg viewBox="0 0 10 10"><path d="M1 3c0-1 1-2 2-2h4c1 0 2 1 2 2v1H7V3H3v1H1z M2 5h6l1 4H1z"/></svg></span><br>
      <span>0400 555 318 <svg viewBox="0 0 10 10"><rect x="3" y="0" width="4" height="10" rx="1"/></svg></span><br>
      <span>clients@meridaleaccts.com.au <svg viewBox="0 0 10 10"><rect x="0" y="2" width="10" height="6"/></svg></span>
    </div>
    <div class="member"><span>Meridale Accountants is a<br>KTR Practise</span><span class="badge"></span></div>
  </section>

</body>
</html>
```